Design a clean homepage for a travel portal based in the US catering to Asians. The design should be able to be used on other pages, or color scheme menu layout, header and footer should be usable on other pages.

Include the main options for users to click, as an example some could be; 1. Local Tour Company 2. Local Tour Guide 3. Transportation Company 4. Tour Packages

Think like www.craftmingle.net who brings designers and clients together we are bringing Tour company, Tour guide, Bus/Transportation company directly to those who need it. This is for a two way portal, not a common one way portal like regular booking sites.

Assume that a person arrives or is planning on arriving at a destination, what are some options that should be on the page, layout of the options: squares, rectangles, stars, scroll slides, whatever makes you feel fun, elegant, fresh, uplifting.

Feelings we want to convey: fun, elegant, fresh, uplifting, interesting, energetic

Update:
When we said this should be a simple design, we meant simple for the end user to understand what was going on. I have attached a screenshot of a website, that it is very easy to understand what its purpose is.

How you decide to set up picture/scenery areas, logo area, menu area, where the options go is all up to you. Would like it to be clean and inviting, we would also like the options to be colors that call the users to action(make them click). This doesn't have to be colors so much as design. If you have further questions feel free to message me.

Attached is our logo in various styles for you to choose from.

Target Market(s)

Travel, package tours, international students, business trips

Industry/Entity Type

Travel Industry

Number of Pages Required

1 page

Colors
ec1f27
ffffff
0255a3
474747
7f7f7f
5c5c5c
aaaaaa

Requirements
Must have
• 1. Local Tour Company 2. Local Tour Guide 3. Transportation Company 4. Tour Packages
Should not have
• Our main goal is not to sell flights or hotel rooms, so this can be an element on the page(or not) but it should not be very central/obvious.

```html
<!DOCTYPE html>
<html lang="en">
<head>
<meta charset="utf-8">
<title>GoVista — Travel Portal</title>
<link rel="stylesheet" href="https://fonts.googleapis.com/css2?family=Open+Sans:wght@400;600;700&family=Kaushan+Script&display=swap">
<style>
:root{
  --red:#ec1f27;
  --red-dark:#b8161c;
  --blue:#0255a3;
  --blue-link:#1e78c8;
  --ink:#474747;
  --ink-mid:#5c5c5c;
  --grey:#7f7f7f;
  --grey-light:#aaaaaa;
  --line:#e4e4e4;
  --band:#f1f1f1;
  --white:#ffffff;
  --footer:#232323;
  --icon:#555555;
  --pie-blue:#7eaeea;
  --pie-red:#ee7b78;
  --pie-green:#cfe88a;
  --pie-purple:#b49ad8;
  --pie-cyan:#8fdcf0;
}
*{box-sizing:border-box;margin:0;padding:0}
html,body{width:1200px;height:2597px;overflow:hidden}
body{font-family:"Open Sans",Arial,sans-serif;color:var(--ink);background:var(--white);position:relative}
h1,h2,h3,h4{font-weight:400}
.abs{position:absolute}

/* header */
.site-header{position:absolute;left:0;top:0;width:1200px;height:120px}
.brand{position:absolute;left:100px;top:42px;display:flex;align-items:center;gap:10px;font-size:24px;font-weight:600;color:var(--blue)}
.brand-dot{width:20px;height:20px;border-radius:50%;background:var(--red)}
.account{position:absolute;left:758px;top:52px;font-size:11px;color:var(--grey);display:flex;gap:20px}
.account span::before{content:"";display:inline-block;width:7px;height:8px;background:var(--blue);margin-right:5px;border-radius:1px}
.btn{display:inline-flex;align-items:center;justify-content:center;color:var(--white);background:linear-gradient(#e2343a,var(--red-dark));border-radius:3px;font-size:13px}
.header-cta{position:absolute;left:915px;top:41px;width:186px;height:39px}

/* nav */
.main-nav{position:absolute;left:0;top:120px;width:1200px;height:58px;border-top:1px solid var(--line);border-bottom:1px solid var(--line)}
.main-nav ul{list-style:none;display:flex;position:absolute;left:97px;top:0;height:57px}
.main-nav li{font-size:11px;text-transform:uppercase;color:var(--ink);display:flex;align-items:center;padding:0 28px;height:57px;white-space:nowrap}
.main-nav li.active{background:#ececec;color:var(--red);padding:0 44px}

/* hero */
.hero{position:absolute;left:0;top:178px;width:1200px;height:557px;overflow:hidden;background:linear-gradient(180deg,#a9cbe8 0%,#dce9f2 28%,#3fa6c8 38%,#1e8fb5 52%,#e9edea 66%,#d9c8a4 80%,#c9b48c 100%)}
.hero-arrow{position:absolute;top:230px}
.bubble{position:absolute;width:112px;height:112px;border-radius:50%;background:radial-gradient(circle at 50% 35%,#fafafa,#cfcfcf);border:4px solid #f4f4f4;box-shadow:0 8px 10px rgba(0,0,0,.25);display:flex;align-items:center;justify-content:center}
.tag{position:absolute;background:var(--white);border-radius:6px;font-family:"Kaushan Script",cursive;color:var(--red);font-size:24px;line-height:34px;padding:6px 14px;box-shadow:0 2px 6px rgba(0,0,0,.2);white-space:nowrap}
.orbit{position:absolute;left:440px;top:225px;width:310px;height:310px;border:2px dashed rgba(255,255,255,.7);border-radius:50%}

/* search */
.search-band{position:absolute;left:0;top:735px;width:1200px;height:155px;background:var(--band)}
.field-label{position:absolute;top:44px;font-size:11px;color:var(--blue-link);text-transform:uppercase}
.field{position:absolute;top:73px;height:34px;background:var(--white);border:1px solid #dcdcdc;font-size:10px;color:#bbb;padding:10px 8px;white-space:nowrap;overflow:hidden}
.field-btn{position:absolute;top:73px;width:28px;height:34px;background:#444;display:flex;align-items:center;justify-content:center}
.search-btn{position:absolute;left:938px;top:73px;width:162px;height:34px;background:var(--blue);color:var(--white);font-size:10px;padding:11px 8px}
.search-btn i{position:absolute;right:0;top:0;width:34px;height:34px;background:var(--red);display:flex;align-items:center;justify-content:center}

/* featured */
.section-title{position:absolute;font-size:20px;color:var(--blue);text-transform:uppercase}
.featured-rule{position:absolute;left:98px;top:977px;width:1004px;height:1px;background:var(--line)}
.card{position:absolute;top:1003px;width:235px;height:359px;border:1px solid #e6e6e6;box-shadow:0 1px 3px rgba(0,0,0,.08);background:var(--white)}
.card-photo{height:152px}
.card-title{position:absolute;left:10px;top:170px;font-size:11px;font-weight:600;text-transform:uppercase;color:var(--ink)}
.card-price{position:absolute;right:12px;top:167px;font-size:15px;color:var(--red)}
.card-rule{position:absolute;left:10px;right:10px;top:195px;height:1px;background:var(--line)}
.stars{position:absolute;left:10px;top:203px;font-size:11px;color:#f2b01e;letter-spacing:1px}
.stars b{color:#ddd;font-weight:400}
.reviews{position:absolute;right:12px;top:205px;font-size:9px;color:var(--grey-light)}
.card-text{position:absolute;left:10px;right:10px;top:237px;font-size:10px;line-height:20px;color:var(--ink-mid)}
.card-actions{position:absolute;left:10px;top:310px;display:flex;gap:4px}
.chip{height:30px;width:76px;color:var(--white);font-size:10px;display:flex;align-items:center;justify-content:center;gap:5px}
.chip.view{background:var(--red)}
.chip.book{background:var(--blue-link)}

/* guide band */
.guide{position:absolute;left:0;top:1410px;width:1200px;height:445px;background:linear-gradient(135deg,#12324f 0%,#2d5a7a 45%,#4f7f8c 70%,#1c3f5e 100%)}
.guide h2{position:absolute;left:98px;top:72px;font-size:21px;color:var(--white);text-transform:uppercase}
.guide .lead{position:absolute;left:98px;top:112px;width:400px;font-size:12px;line-height:22px;color:#e8eef4}
.guide .body{position:absolute;left:98px;top:166px;width:400px;font-size:10px;line-height:19px;color:#d8e2ea}
.guide-cta{position:absolute;left:100px;top:310px;width:188px;height:40px}
.snap{position:absolute;border:5px solid var(--white);border-radius:4px;box-shadow:0 3px 8px rgba(0,0,0,.35)}

/* stats */
.stats-lead{position:absolute;left:110px;top:1920px;width:530px;text-align:right;font-size:12px;line-height:22px;color:var(--ink)}
.stats-body{position:absolute;left:110px;width:530px;text-align:right;font-size:10px;line-height:20px;color:var(--grey)}
.stats-cta{position:absolute;left:451px;top:2152px;width:188px;height:40px}
.pie-title{position:absolute;left:1004px;top:1866px;font-size:20px;color:var(--blue-link)}
.legend{position:absolute;left:680px;top:1973px;list-style:none}
.legend li{font-size:12px;color:var(--ink);height:34.5px;text-align:right;width:150px;position:relative;padding-right:25px}
.legend li i{position:absolute;right:0;top:5px;width:9px;height:9px;border-radius:50%}

/* footer */
.site-footer{position:absolute;left:0;top:2190px;width:1200px;height:407px}
.foot-col{position:absolute;top:110px}
.foot-col h4{font-size:13px;color:var(--white);text-transform:uppercase;margin-bottom:18px}
.foot-col li{list-style:none;font-size:11px;color:#ddd;height:26px}
.foot-divider{position:absolute;top:110px;width:1px;height:150px;background:#3a3a3a}
.news-note{font-size:11px;color:#ddd;margin-top:-8px}
.news-input{margin-top:12px;width:278px;height:36px;background:var(--white);border-radius:3px;font-size:11px;color:var(--ink);padding:10px 14px}
.news-btn{margin-top:10px;width:133px;height:40px;font-size:12px;text-transform:uppercase}
.copyright{position:absolute;left:98px;top:362px;font-size:11px;color:#ccc}
.social{position:absolute;left:843px;top:354px;display:flex;align-items:center;gap:6px;font-size:11px;color:#ccc}
.social i{width:32px;height:32px;border-radius:50%;border:2px solid #fff;background:var(--blue-link)}
.social i.r{background:var(--red)}
.page-code{position:absolute;left:1144px;top:362px;font-size:11px;color:#ccc}
</style>
</head>
<body>

<header class="site-header">
  <div class="brand"><span class="brand-dot"></span>GoVista</div>
  <div class="account"><span>Login</span><span>Register</span></div>
  <a class="btn header-cta">Make Trip To Register</a>
</header>

<nav class="main-nav">
  <ul>
    <li class="active">Home</li>
    <li>Local Tour Company</li>
    <li>Local Tour Guide</li>
    <li>Transportation</li>
    <li>Tour Packages</li>
    <li>Hotel/Flight</li>
    <li>Contact Us</li>
  </ul>
</nav>

<section class="hero">
  <div class="abs" role="img" aria-label="Travellers on a tropical beach with turquoise sea" style="left:0;top:0;width:1200px;height:557px"></div>
  <div class="orbit"></div>
  <svg class="hero-arrow" style="left:48px" width="26" height="90" viewBox="0 0 26 90"><path d="M22 2 L4 45 L22 88" fill="none" stroke="#fff" stroke-width="2"/></svg>
  <svg class="hero-arrow" style="left:1126px" width="26" height="90" viewBox="0 0 26 90"><path d="M4 2 L22 45 L4 88" fill="none" stroke="#fff" stroke-width="2"/></svg>

  <div class="tag" style="left:198px;top:88px">Tour Company</div>
  <div class="bubble" style="left:398px;top:56px">
    <svg width="44" height="44" viewBox="0 0 44 44"><path d="M4 16 L22 4 L40 16 Z" fill="#555"/><rect x="6" y="18" width="32" height="4" fill="#555"/><g fill="#555"><rect x="9" y="23" width="4" height="14"/><rect x="17" y="23" width="4" height="14"/><rect x="25" y="23" width="4" height="14"/><rect x="33" y="23" width="4" height="14"/></g><rect x="4" y="38" width="36" height="4" fill="#555"/></svg>
  </div>
  <div class="bubble" style="left:678px;top:56px">
    <svg width="40" height="44" viewBox="0 0 40 44"><rect x="8" y="2" width="3" height="40" fill="#555"/><path d="M11 4 H34 L28 12 L34 20 H11 Z" fill="#555"/></svg>
  </div>
  <div class="tag" style="left:817px;top:88px">Tour Guide</div>

  <div class="tag" style="left:130px;top:290px">Transport</div>
  <div class="bubble" style="left:306px;top:262px">
    <svg width="50" height="40" viewBox="0 0 50 40"><rect x="4" y="4" width="42" height="26" rx="4" fill="#555"/><g fill="#ccc"><rect x="8" y="8" width="9" height="8"/><rect x="20" y="8" width="9" height="8"/><rect x="32" y="8" width="10" height="8"/></g><circle cx="14" cy="32" r="5" fill="#333"/><circle cx="36" cy="32" r="5" fill="#333"/></svg>
  </div>
  <div class="bubble" style="left:786px;top:262px">
    <svg width="46" height="42" viewBox="0 0 46 42"><path d="M16 10 V5 H30 V10" fill="none" stroke="#555" stroke-width="3"/><rect x="3" y="10" width="40" height="28" rx="3" fill="#555"/><rect x="3" y="20" width="40" height="3" fill="#ccc"/></svg>
  </div>
  <div class="tag" style="left:918px;top:290px">Tour Packages</div>
</section>

<section class="search-band">
  <span class="field-label" style="left:99px">Your Destination</span>
  <div class="field" style="left:99px;width:242px">Enter City or Attraction</div>

  <span class="field-label" style="left:356px">Arrival</span>
  <div class="field" style="left:356px;width:138px">mm/dd/yy</div>
  <div class="field-btn" style="left:486px"><svg width="10" height="10" viewBox="0 0 10 10"><rect x="1" y="2" width="8" height="7" fill="none" stroke="#fff"/></svg></div>

  <span class="field-label" style="left:536px">Departure</span>
  <div class="field" style="left:536px;width:136px">mm/dd/yy</div>
  <div class="field-btn" style="left:664px"><svg width="10" height="10" viewBox="0 0 10 10"><rect x="1" y="2" width="8" height="7" fill="none" stroke="#fff"/></svg></div>

  <span class="field-label" style="left:716px">Travelers</span>
  <div class="field" style="left:716px;width:68px">01</div>
  <div class="field-btn" style="left:776px"><svg width="8" height="5" viewBox="0 0 8 5"><path d="M0 0 H8 L4 5 Z" fill="#fff"/></svg></div>

  <span class="field-label" style="left:827px">Service</span>
  <div class="field" style="left:827px;width:68px">Guide</div>
  <div class="field-btn" style="left:887px"><svg width="8" height="5" viewBox="0 0 8 5"><path d="M0 0 H8 L4 5 Z" fill="#fff"/></svg></div>

  <div class="search-btn">Find Tours<i><svg width="11" height="11" viewBox="0 0 11 11"><circle cx="4.5" cy="4.5" r="3.5" fill="none" stroke="#fff" stroke-width="1.5"/><path d="M7 7 L10 10" stroke="#fff" stroke-width="1.5"/></svg></i></div>
</section>

<h2 class="section-title" style="left:98px;top:934px">Featured Tour Activities</h2>
<svg class="abs" style="left:1080px;top:942px" width="22" height="12" viewBox="0 0 22 12"><path d="M6 2 L2 6 L6 10 M16 2 L20 6 L16 10" fill="none" stroke="#aaa" stroke-width="1.5"/></svg>
<div class="featured-rule"></div>

<article class="card" style="left:98px">
  <div class="card-photo" role="img" aria-label="City walking tour through historic streets" style="background:linear-gradient(135deg,#8a6a4a,#d9c3a0 60%,#f3ead8)"></div>
  <h3 class="card-title">City Walking Tour</h3><span class="card-price">$78</span>
  <div class="card-rule"></div>
  <div class="stars">★★★★<b>★</b></div><span class="reviews">150 Reviews</span>
  <p class="card-text">Consectetur adipiscing elit, sed do eiusmod tempor incididunt ut labore et dolore magna aliqua. Ut enim ad minim veniam...</p>
  <div class="card-actions"><span class="chip view">VIEW</span><span class="chip book">BOOK</span></div>
</article>
<article class="card" style="left:355px">
  <div class="card-photo" role="img" aria-label="Coastal village day trip" style="background:linear-gradient(180deg,#2c5f9c,#7fb0d8 45%,#e9e6de 70%,#3f8fb8)"></div>
  <h3 class="card-title">Coastal Day Trip</h3><span class="card-price">$98</span>
  <div class="card-rule"></div>
  <div class="stars">★★★★<b>★</b></div><span class="reviews">150 Reviews</span>
  <p class="card-text">Consectetur adipiscing elit, sed do eiusmod tempor incididunt ut labore et dolore magna aliqua. Ut enim ad minim veniam...</p>
  <div class="card-actions"><span class="chip view">VIEW</span><span class="chip book">BOOK</span></div>
</article>
<article class="card" style="left:611px">
  <div class="card-photo" role="img" aria-label="Museum and culture tour" style="background:linear-gradient(135deg,#b89a72,#efe3cc 55%,#d4c1a0)"></div>
  <h3 class="card-title">Museum Culture Tour</h3><span class="card-price">$88</span>
  <div class="card-rule"></div>
  <div class="stars">★★★★<b>★</b></div><span class="reviews">150 Reviews</span>
  <p class="card-text">Consectetur adipiscing elit, sed do eiusmod tempor incididunt ut labore et dolore magna aliqua. Ut enim ad minim veniam...</p>
  <div class="card-actions"><span class="chip view">VIEW</span><span class="chip book">BOOK</span></div>
</article>
<article class="card" style="left:868px">
  <div class="card-photo" role="img" aria-label="Sunset harbour cruise" style="background:linear-gradient(180deg,#3b5f93,#9cb7d6 40%,#e8c08a 55%,#3f6d8f)"></div>
  <h3 class="card-title">Sunset Harbour Cruise</h3><span class="card-price">$68</span>
  <div class="card-rule"></div>
  <div class="stars">★★★★<b>★</b></div><span class="reviews">150 Reviews</span>
  <p class="card-text">Consectetur adipiscing elit, sed do eiusmod tempor incididunt ut labore et dolore magna aliqua. Ut enim ad minim veniam...</p>
  <div class="card-actions"><span class="chip view">VIEW</span><span class="chip book">BOOK</span></div>
</article>

<section class="guide" role="img" aria-label="Blurred globe with an airplane in the sky">
  <h2>Local Tour Guide</h2>
  <p class="lead">Sed ut perspiciatis unde omnis iste natus error sit voluptatem accusantium doloremque laudantium, totam...</p>
  <p class="body">Lorem ipsum dolor sit amet, consectetur adipiscing elit, sed do eiusmod tempor incididunt ut labore et dolore magna aliqua. Ut enim ad minim veniam, quis nostrud exercitation ullamco laboris nisi ut aliquip ex ea commodo consequat. Duis aute irure dolor in reprehenderit in voluptate velit esse cillum dolore eu fugiat nulla pariatur. Excepteur sint occaecat cupidatat non proident, sunt in culpa qui officia deserunt mollit anim id est laborum.</p>
  <a class="btn guide-cta">Make Trip To Register</a>

  <div class="snap" role="img" aria-label="Traveller with a colourful umbrella on a pier" style="left:512px;top:65px;width:245px;height:150px;transform:rotate(-8deg);background:linear-gradient(135deg,#8fb7d9,#d8e6ef 55%,#7a8fa0)"></div>
  <div class="snap" role="img" aria-label="Friends jumping on a beach" style="left:765px;top:65px;width:270px;height:160px;transform:rotate(5deg);background:linear-gradient(180deg,#6fa9db,#bcd8ee 60%,#d9c9a6)"></div>
  <div class="snap" role="img" aria-label="Family in a swimming pool" style="left:570px;top:235px;width:172px;height:118px;background:linear-gradient(180deg,#5fb3df,#2a8fc8)"></div>
  <div class="snap" role="img" aria-label="Couple outdoors among trees" style="left:752px;top:235px;width:170px;height:118px;background:linear-gradient(135deg,#6f8f4e,#b8c99a)"></div>
  <div class="snap" role="img" aria-label="Family lying on grass" style="left:932px;top:235px;width:170px;height:118px;background:linear-gradient(180deg,#9ccf6a,#5e9f3a)"></div>
</section>
<svg class="abs" style="left:0;top:1815px" width="1200" height="45" viewBox="0 0 1200 45"><path d="M0 45 V28 Q300 -5 600 20 T1200 6 V45 Z" fill="#fff"/></svg>

<p class="stats-lead">Nemo enim ipsam voluptatem quia voluptas sit aspernatur aut odit aut fugit, sed quia consequuntur magni dolores eos qui ratione voluptatem sequi nesciunt...</p>
<p class="stats-body" style="top:1973px">Molestias excepturi sint occaecati cupiditate non provident, similique sunt in culpa qui officia deserunt mollitia animi, id est laborum et dolorum fuga. Et harum quidem rerum facilis est et expedita distinctio. Nam libero tempore, cum soluta nobis est eligendi optio cumque nihil impedit quo minus id quod maxime placeat facere possimus, omnis voluptas assumenda est, omnis dolor repellendus. Temporibus autem quibusdam et aut officiis.</p>
<p class="stats-body" style="top:2065px">Assumenda est, omnis dolor repellendus. Temporibus autem quibusdam et aut officiis debitis aut rerum necessitatibus saepe eveniet ut et voluptates repudiandae sint et molestiae non recusandae. Itaque earum rerum hic tenetur a sapiente delectus, ut aut reiciendis voluptatibus maiores alias consequatur aut perferendis...</p>
<a class="btn stats-cta">Click View More Details</a>

<h2 class="pie-title">Pie Charts</h2>
<ul class="legend">
  <li>Loading<i style="background:var(--pie-blue)"></i></li>
  <li>Food<i style="background:var(--pie-red)"></i></li>
  <li>Entertainment<i style="background:var(--pie-green)"></i></li>
  <li>Transport<i style="background:var(--pie-purple)"></i></li>
  <li>Misc<i style="background:var(--pie-cyan)"></i></li>
</ul>
<svg class="abs" style="left:835px;top:1920px" width="280" height="300" viewBox="-140 -140 280 300">
  <ellipse cx="0" cy="18" rx="130" ry="130" fill="#c9c9c9"/>
  <g stroke="#fff" stroke-width="1">
    <path d="M0 0 L0 -130 A130 130 0 0 1 123.6 40.2 Z" fill="#7eaeea"/>
    <path d="M0 0 L123.6 40.2 A130 130 0 0 1 -40.2 123.6 Z" fill="#ee7b78"/>
    <path d="M0 0 L-40.2 123.6 A130 130 0 0 1 -120.9 47.9 Z" fill="#cfe88a"/>
    <path d="M0 0 L-120.9 47.9 A130 130 0 0 1 -89 -94.8 Z" fill="#b49ad8"/>
    <path d="M0 0 L-89 -94.8 A130 130 0 0 1 0 -130 Z" fill="#8fdcf0"/>
  </g>
  <g font-family="Open Sans, sans-serif" font-size="13" font-weight="700" fill="#222" text-anchor="middle">
    <text x="66" y="-42">30%</text>
    <text x="37" y="73">25%</text>
    <text x="-55" y="61">14%</text>
    <text x="-78" y="-13">19%</text>
    <text x="-30" y="-69">12%</text>
  </g>
</svg>

<footer class="site-footer">
  <svg class="abs" style="left:0;top:0" width="1200" height="407" viewBox="0 0 1200 407"><path d="M0 40 Q300 10 600 22 T1200 0 V407 H0 Z" fill="#232323"/></svg>
  <div class="foot-col" style="left:98px"><h4>Company</h4><ul><li>Our story</li><li>Why Products</li><li>Order Now</li><li>Testimonials</li><li>Best Sellings</li></ul></div>
  <div class="foot-divider" style="left:265px"></div>
  <div class="foot-col" style="left:355px"><h4>Products</h4><ul><li>Alandit sed nulla</li><li>In ullamcorper</li><li>Est eget tempor</li><li>Cursus neque</li><li>Consectetuer</li></ul></div>
  <div class="foot-divider" style="left:522px"></div>
  <div class="foot-col" style="left:598px"><h4>Support</h4><ul><li>FAQs</li><li>Privacy Policy</li><li>Recommendations</li><li>Contact</li></ul></div>
  <div class="foot-divider" style="left:755px"></div>
  <div class="foot-col" style="left:822px"><h4>Sign Up Newsletter</h4>
    <p class="news-note">Please sign up here for latest deals</p>
    <div class="news-input">Email address</div>
    <a class="btn news-btn">Subscribe</a>
  </div>
  <p class="copyright">© 2015 GoVista. All right reserved &nbsp;Term of Use</p>
  <div class="social">Connect With Us: <i></i><i></i><i></i><i class="r"></i></div>
  <span class="page-code">C11</span>
</footer>

</body>
</html>
```